Rosko Tamblin

I am a songwriter and would like to include a bio, pictures, discography, CD covers and access to some of my music

Target Market(s)

Music Lovers, songwriters publishers

Coding

Coded - Design and coding required

Number of Pages Required

5+ page

Requirements
Must have
• Pictures of my CD covers, pictures of me and either my Music or links to my music
Nice to have
Should not have
• cartoons

```html
<!DOCTYPE html>
<html lang="en">
<head>
<meta charset="utf-8">
<title>Rosko Tamblin — Songwriter</title>
<link rel="stylesheet" href="https://fonts.googleapis.com/css2?family=Krona+One&family=Lato:ital,wght@0,400;0,700;1,400&family=Roboto:wght@400;500&display=swap">
<style>
:root{
  --black:#000;
  --white:#fff;
  --coral:#f34d4d;
  --coral-soft:#ff5a52;
  --star:#f5b400;
  --field:#141414;
}
*{box-sizing:border-box;margin:0;padding:0}
html,body{width:1200px;height:3530px;overflow:hidden;background:var(--black)}
body{position:relative;font-family:"Lato",sans-serif;color:var(--white)}
.abs{position:absolute}
.display{font-family:"Krona One",sans-serif;font-weight:400}

/* Header & hero */
.hero{position:absolute;left:0;top:0;width:1200px;height:603px;overflow:hidden;
  background:radial-gradient(ellipse 60% 45% at 20% 80%,#ff9a1a 0%,#e0420b 35%,rgba(120,20,0,.6) 65%,transparent 85%),
  radial-gradient(ellipse 55% 40% at 80% 90%,#ff7a10 0%,#b5300a 45%,transparent 80%),
  linear-gradient(180deg,#0d0604 0%,#2a0e05 45%,#5a1a06 70%,#8a2c08 100%)}
.hero-person{left:600px;top:170px;width:380px;height:433px;border-radius:190px 190px 0 0;
  background:linear-gradient(180deg,#d59a7a 0%,#c98c6c 25%,#e8e6e2 45%,#cfcac3 70%,#2a2422 100%)}
.logo{left:110px;top:30px;font-size:25px;letter-spacing:.5px}
.nav{font-size:15px;font-weight:700}
.nav a{color:var(--white);text-decoration:none;position:absolute;white-space:nowrap}
.nav a.active{color:var(--coral)}
.social{left:946px;top:32px;display:flex;gap:6px}
.social span{width:30px;height:30px;border:1.5px solid var(--white);border-radius:50%;display:block}
.hero-title{left:108px;top:200px;font-size:48px}
.hero-text{left:111px;top:272px;font-size:17px;line-height:31px;width:440px}
.btn-coral{left:111px;top:352px;width:274px;height:58px;border-radius:29px;background:var(--coral-soft);
  font-weight:700;font-size:16px;display:flex;align-items:center;justify-content:center;letter-spacing:.2px}

/* About */
.about-ring{left:131px;top:688px;width:386px;height:386px;border-radius:50%;border:7px solid transparent;border-left-color:var(--coral);border-bottom-color:var(--coral);transform:rotate(20deg)}
.about-photo{left:138px;top:686px;width:376px;height:376px;border-radius:50%;
  background:radial-gradient(circle at 55% 35%,#e8e4de 0%,#cdbfae 30%,#9a7a58 60%,#6e5238 100%)}
.about-title{left:559px;top:700px;font-size:34px}
.about-text{left:559px;top:752px;width:508px;font-size:14.2px;line-height:28.3px;text-align:justify}
.btn-outline{border:2px solid var(--white);border-radius:30px;display:flex;align-items:center;justify-content:center;font-weight:700}
.about-btn{left:560px;top:1007px;width:185px;height:57px;font-size:16px}

/* CD art */
.cd-art{left:0;top:1162px;width:1200px;height:649px;
  background:radial-gradient(ellipse 50% 45% at 50% 40%,rgba(210,90,170,.55),transparent 70%),
  radial-gradient(ellipse 30% 60% at 15% 70%,rgba(80,30,110,.7),transparent 80%),
  radial-gradient(ellipse 30% 60% at 85% 70%,rgba(90,30,120,.7),transparent 80%),
  linear-gradient(180deg,#1c1430 0%,#2a1838 50%,#120c1c 100%)}
.section-title{width:1200px;left:0;text-align:center;font-size:34px}
.section-sub{width:1200px;left:0;text-align:center;font-size:16px;line-height:27px}
.disc{width:208px;height:208px;border-radius:50%}
.disc::after{content:"";position:absolute;left:96px;top:96px;width:16px;height:16px;border-radius:50%;background:var(--white)}
.disc-1{left:112px;top:1376px;background:radial-gradient(circle at 40% 50%,#ddd 0%,#777 40%,#1a1a1a 90%)}
.disc-2{left:369px;top:1376px;background:linear-gradient(180deg,#111 0%,#2a1208 40%,#ff6a12 60%,#7a1e05 80%,#151010 100%)}
.disc-3{left:623px;top:1376px;background:radial-gradient(circle at 50% 45%,#f0c0a0 0%,#38c26a 40%,#c23a7a 80%,#3a8a30 100%)}
.disc-4{left:880px;top:1376px;background:conic-gradient(#e53020,#f0d020,#2050c0,#e53020,#20a040,#f0d020,#e53020)}
.disc-label{width:240px;text-align:center;font-family:"Roboto",sans-serif}
.disc-name{font-size:21px;font-weight:500;top:1604px}
.disc-date{font-size:18px;top:1637px}
.arrow{width:22px;height:40px}
.cd-btn{left:463px;top:1692px;width:274px;height:46px;font-size:13px}

/* Discography */
.cover{width:315px;height:274px}
.c1{left:111px;top:2025px;background:linear-gradient(135deg,#e8506a 0%,#7a3ab0 40%,#2a9ae0 70%,#f0a040 100%)}
.c2{left:441px;top:2025px;background:linear-gradient(160deg,#f6c21a 0%,#e24a14 35%,#3a3a3a 70%,#c9c2b0 100%)}
.c3{left:771px;top:2025px;background:linear-gradient(180deg,#3a3c48 0%,#6a6e80 35%,#2a1c18 70%,#a0401a 100%)}
.c4{left:111px;top:2315px;background:linear-gradient(160deg,#c88a3a 0%,#e0a050 35%,#2a5a8a 70%,#f0b040 100%)}
.c5{left:441px;top:2315px;background:linear-gradient(180deg,#1a3050 0%,#6a8aa0 45%,#d8e4ea 60%,#20364a 85%,#7a6030 100%)}
.c6{left:771px;top:2315px;background:linear-gradient(160deg,#f2ecdc 0%,#c8d0e0 40%,#e4b8a8 70%,#f0e8d0 100%)}

/* Reviews */
.reviews{left:0;top:2685px;width:1200px;height:443px;
  background:radial-gradient(ellipse 40% 50% at 30% 20%,rgba(120,110,200,.45),transparent 70%),
  radial-gradient(ellipse 40% 50% at 75% 25%,rgba(200,90,150,.35),transparent 70%),
  linear-gradient(180deg,#24214a 0%,#1b1838 60%,#0c0a18 100%)}
.eyebrow{left:0;width:1200px;text-align:center;top:2768px;font-size:16px;letter-spacing:3px}
.review-title{left:0;width:1200px;text-align:center;top:2802px;font-size:29px}
.avatar{left:215px;top:2869px;width:104px;height:104px;border-radius:50%;background:linear-gradient(180deg,#e8e8e8 0%,#c8c8c8 55%,#1e2a3a 100%)}
.reviewer{left:167px;top:2980px;width:200px;text-align:center;font-size:16.5px;line-height:23px}
.stars{left:240px;top:3030px;color:var(--star);font-size:11px;letter-spacing:1px}
.quote{left:377px;top:2883px;width:600px;font-size:15.3px;font-style:italic;line-height:28.3px}
.qmark{font-family:Georgia,serif;font-size:54px;color:#8a8aa0;line-height:1}
.dots{left:568px;top:3030px;display:flex;gap:6px}
.dots span{width:12px;height:12px;border-radius:50%;background:#9a9aa8}
.dots span.on{background:var(--white)}
.side-btn{width:96px;height:96px;border-radius:50%;background:rgba(255,255,255,.15);top:2880px}

/* Footer */
.foot-head{top:3205px;font-size:16px;font-weight:700;text-transform:uppercase}
.foot-text{font-size:14.5px;line-height:27px}
.field{left:425px;width:276px;height:38px;background:var(--field);font-size:14px;padding:10px 12px;border:1px solid #1f1f1f}
.subscribe{left:425px;top:3400px;width:276px;height:38px;background:var(--coral);font-size:16px;font-weight:700;display:flex;align-items:center;justify-content:center}
.read{color:var(--coral);text-decoration:underline}
.copyright{left:0;width:1200px;text-align:center;top:3476px;font-size:14.5px}
</style>
</head>
<body>

<header>
  <section class="hero" aria-label="Hero">
    <div class="abs hero-person" role="img" aria-label="Photo of Rosko Tamblin standing before a glowing fire crater at night"></div>
  </section>
  <div class="abs logo display">Rosko Tamblin</div>
  <nav class="abs nav" style="left:0;top:34px">
    <a class="active" style="left:459px">Bio</a>
    <a style="left:520px">Pictures</a>
    <a style="left:615px">Discography</a>
    <a style="left:741px">Cd Covers</a>
    <a style="left:851px">My Music</a>
  </nav>
  <div class="abs social" aria-label="Social links"><span></span><span></span><span></span><span></span></div>
  <h1 class="abs hero-title display">Rosko Tamblin</h1>
  <p class="abs hero-text">Lorem ipsum dolor sit amet, consectetur adipiscing elit, sed do eiusmod tempor incididunt</p>
  <div class="abs btn-coral">KNOW MORE ABOUT ME</div>
</header>

<section class="about">
  <div class="abs about-ring"></div>
  <div class="abs about-photo" role="img" aria-label="Portrait of Rosko Tamblin in a white shirt holding a hat"></div>
  <h2 class="abs about-title display">About Rosko Tamblin</h2>
  <p class="abs about-text">Rosko Tamblin was born and raised in Houston, Texas. He began playing music at the age of eight when his sister returned home from summer camp and asked her parents to buy her a baritone ukulele. She taught her younger brother some chords on the ukulele and he was hooked. The following spring, they went to one of the border towns in Mexico and bought a Mexican guitar for $12. They restrung it with nylon strings and Tamblin began to learn how to play the guitar. He took guitar lessons at a local music store and learned how to play the hits of the day by groups like the Harbour Lights, the Wayfarers, and the Moonlarks.</p>
  <div class="abs btn-outline about-btn">LEARN MORE</div>
</section>

<section class="cd-section">
  <div class="abs cd-art" role="img" aria-label="Concert stage with purple lights and laser beams"></div>
  <h2 class="abs section-title display" style="top:1246px">CD ART</h2>
  <p class="abs section-sub" style="top:1292px">Lorem ipsum dolor sit amet, consectetur adipiscing elit, sed do eiusmod<br>tempor incididunt ut labore et dolore magna aliqua.</p>
  <svg class="abs arrow" style="left:60px;top:1468px" viewBox="0 0 22 40"><path d="M18 4 4 20l14 16" fill="none" stroke="#fff" stroke-width="2"/></svg>
  <svg class="abs arrow" style="left:1112px;top:1468px" viewBox="0 0 22 40"><path d="M4 4l14 16L4 36" fill="none" stroke="#fff" stroke-width="2"/></svg>
  <div class="abs disc disc-1" role="img" aria-label="CD disc art, black and white guitarist"></div>
  <div class="abs disc disc-2" role="img" aria-label="CD disc art, fire crater at night"></div>
  <div class="abs disc disc-3" role="img" aria-label="CD disc art with guitarist in bright colours"></div>
  <div class="abs disc disc-4" role="img" aria-label="CD disc art, colourful pattern"></div>
  <div class="abs disc-label disc-name" style="left:96px">Pines Past Dawn</div>
  <div class="abs disc-label disc-date" style="left:96px">5-4-19</div>
  <div class="abs disc-label disc-name" style="left:353px">Pines Past Dawn</div>
  <div class="abs disc-label disc-date" style="left:353px">5-4-19</div>
  <div class="abs disc-label disc-name" style="left:613px">Tamblins&nbsp; CD</div>
  <div class="abs disc-label disc-date" style="left:607px">5-4-19</div>
  <div class="abs disc-label disc-name" style="left:871px">Open Doorways</div>
  <div class="abs disc-label disc-date" style="left:869px">11-9-19</div>
  <div class="abs btn-outline cd-btn">LISTEN FROM STORMY HOURS</div>
</section>

<section class="discography">
  <h2 class="abs section-title display" style="top:1892px">DISCOGRAPHY</h2>
  <p class="abs section-sub" style="top:1938px">Lorem ipsum dolor sit amet, consectetur adipiscing elit, sed do eiusmod<br>tempor incididunt ut labore et dolore magna aliqua.</p>
  <div class="abs cover c1" role="img" aria-label="Album cover: musician with guitar on a colourful swirl"></div>
  <div class="abs cover c2" role="img" aria-label="Album cover: burning newspaper beside coffee cup"></div>
  <div class="abs cover c3" role="img" aria-label="Album cover Stormy Hours: silhouette under lightning storm"></div>
  <div class="abs cover c4" role="img" aria-label="Album cover Harbor Light Road: seashells and song list"></div>
  <div class="abs cover c5" role="img" aria-label="Album cover Harbor Light Road: stormy sea and waves"></div>
  <div class="abs cover c6" role="img" aria-label="Album cover Small Town Summers: collage of childhood photos"></div>
</section>

<section class="testimonials">
  <div class="abs reviews" role="img" aria-label="Crowd at a concert under stage lights"></div>
  <div class="abs eyebrow">REVIEWS</div>
  <h2 class="abs review-title display">WHAT OUR CUSTOMERS ARE SAYING</h2>
  <div class="abs side-btn" style="left:-48px"></div>
  <div class="abs side-btn" style="left:1152px"></div>
  <svg class="abs" style="left:8px;top:2914px" width="14" height="26" viewBox="0 0 14 26"><path d="M12 2 2 13l10 11" fill="none" stroke="#fff" stroke-width="1.6"/></svg>
  <svg class="abs" style="left:1176px;top:2914px" width="14" height="26" viewBox="0 0 14 26"><path d="M2 2l10 11L2 24" fill="none" stroke="#fff" stroke-width="1.6"/></svg>
  <div class="abs avatar" role="img" aria-label="Reviewer portrait"></div>
  <div class="abs reviewer">Marco Vellani,<br>KRL Studio Bass</div>
  <div class="abs stars">★★★★★</div>
  <div class="abs qmark" style="left:340px;top:2866px">&ldquo;</div>
  <p class="abs quote">At this point I have developed a continuous creative relationship with Rosko and have recorded on approximately 30 songs of his. He writes well-structured songs that allow me to flex my creative muscles. Rosko knows how to make his original ideas blossom into fully constructed arrangements that sound great</p>
  <div class="abs qmark" style="left:778px;top:2966px">&rdquo;</div>
  <div class="abs dots"><span class="on"></span><span></span><span></span><span></span></div>
</section>

<footer>
  <h3 class="abs foot-head" style="left:114px">Contact Us</h3>
  <p class="abs foot-text" style="left:114px;top:3240px">123 Avenue name, City name<br>10150, United States</p>
  <p class="abs foot-text" style="left:114px;top:3300px">888 888 8888<br>info@roskotamblin.com</p>

  <h3 class="abs foot-head" style="left:428px">Rosko Tamblin Newsletter</h3>
  <p class="abs foot-text" style="left:425px;top:3240px">Lorem ipsum dolor sit amet, consectetur<br>adipiscing elit, sed do eiusmod</p>
  <div class="abs field" style="top:3308px">Name</div>
  <div class="abs field" style="top:3355px">Email</div>
  <div class="abs subscribe">SUBSCRIBE</div>

  <h3 class="abs foot-head" style="left:808px">Our Latest Music</h3>
  <p class="abs foot-text" style="left:808px;top:3240px">Lorem ipsum dolor sit amet, consectetur<br>adipiscing elit, sed do eiuor , consectetur<br>adipiscing elit, <span class="read">Read More</span></p>

  <p class="abs copyright">Copyright © 2020. All Rights Reserved</p>
</footer>

</body>
</html>
```